Walk Beside The River

Business Card design

Target Market(s)

People who require support in the commnity

Industry/Entity Type

Mental Health Support

Contact Information for Business Card

Mental Health Support Rosalind Tavener walkbesidetheriver@mailcove.com.au 0481 637 092 PO Box 926 Wattlecombe SA 5291

Colors
6B429C
8869AF
B7A5CE
E3DAEB
F3F0F8

Requirements
Must have
• Logo & details listed above
Should not have
• No red or orange

```html
<!DOCTYPE html>
<html lang="en">
<head>
<meta charset="utf-8">
<title>Walk Beside The River — Business Card</title>
<link href="https://fonts.googleapis.com/css2?family=Lato:wght@400;900&display=swap" rel="stylesheet">
<style>
  :root {
    --purple: #6B429C;
    --purple-mid: #8869AF;
    --lilac: #B7A5CE;
    --lilac-soft: #E3DAEB;
    --white: #FFFFFF;
    --cream: #F6F0DC;
    --sun: #F5EC2A;
    --backdrop: #2E2E30;
  }
  * { box-sizing: border-box; margin: 0; padding: 0; }
  html, body {
    width: 1200px; height: 875px; overflow: hidden;
    background: var(--backdrop);
    font-family: "Lato", Arial, sans-serif;
  }
  .stage { position: relative; width: 1200px; height: 875px; }

  .card {
    position: absolute;
    width: 525px; height: 300px;
    border-radius: 18px;
    overflow: hidden;
    box-shadow: 0 18px 40px rgba(0,0,0,0.45);
  }

  /* Front */
  .card-front {
    left: 70px; top: 120px;
    background: var(--purple);
    display: flex; align-items: center; justify-content: center;
  }
  .brand {
    display: flex; flex-direction: column; align-items: center; gap: 18px;
  }
  .brand-dot {
    width: 46px; height: 46px; border-radius: 50%;
    background: var(--sun);
  }
  .brand-name {
    color: var(--cream);
    font-weight: 400;
    font-size: 19px;
    letter-spacing: 0.32em;
    text-transform: uppercase;
  }

  /* Back */
  .card-back {
    left: 605px; top: 455px;
    background: var(--white);
  }
  .back-accent {
    position: absolute;
    left: -70px; top: 40px;
    width: 300px; height: 300px;
    border-radius: 50%;
    background: var(--purple);
  }
  .details {
    position: absolute;
    right: 30px; top: 46px;
    text-align: right;
    color: var(--purple);
  }
  .person-name {
    font-weight: 900;
    font-size: 30px;
    letter-spacing: -0.01em;
    text-transform: uppercase;
    line-height: 1;
  }
  .person-role {
    font-size: 17px;
    margin-top: 4px;
  }
  .contact-list { list-style: none; margin-top: 26px; }
  .contact-item {
    display: flex; justify-content: flex-end; align-items: center; gap: 8px;
    font-size: 14px; line-height: 1.55;
  }
  .contact-item.phone { font-size: 21px; font-weight: 400; }
  .contact-icon { width: 13px; height: 13px; fill: var(--purple); flex: none; }
</style>
</head>
<body>
<main class="stage">
  <section class="card card-front" aria-label="Card front">
    <div class="brand">
      <span class="brand-dot" aria-hidden="true"></span>
      <span class="brand-name">Walk Beside The River</span>
    </div>
  </section>

  <section class="card card-back" aria-label="Card back">
    <div class="back-accent" aria-hidden="true"></div>
    <div class="details">
      <h1 class="person-name">Rosalind Tavener</h1>
      <p class="person-role">Mental Health Support</p>
      <ul class="contact-list">
        <li class="contact-item phone">0481 637 092
          <svg class="contact-icon" viewBox="0 0 24 24" aria-hidden="true"><path d="M6.6 10.8a15.2 15.2 0 0 0 6.6 6.6l2.2-2.2a1 1 0 0 1 1-.25 11.4 11.4 0 0 0 3.6.57 1 1 0 0 1 1 1V20a1 1 0 0 1-1 1A17 17 0 0 1 3 4a1 1 0 0 1 1-1h3.5a1 1 0 0 1 1 1c0 1.250.2 2.450.57 3.57a1 1 0 0 1-.25 1z"/></svg>
        </li>
        <li class="contact-item">walkbesidetheriver@mailcove.com.au
          <svg class="contact-icon" viewBox="0 0 24 24" aria-hidden="true"><path d="M2 5h20v14H2z M4 7v.4l8 5 8-5V7z" fill-rule="evenodd"/></svg>
        </li>
        <li class="contact-item">PO Box 926 Wattlecombe SA 5291
          <svg class="contact-icon" viewBox="0 0 24 24" aria-hidden="true"><path d="M12 2a7 7 0 0 0-7 7c0 5.2 7 13 7 13s7-7.8 7-13a7 7 0 0 0-7-7zm0 9.5A2.5 2.5 0 1 1 12 6.5a2.5 2.5 0 0 1 0 5z"/></svg>
        </li>
      </ul>
    </div>
  </section>
</main>
</body>
</html>
```